Modern Business Card

Modern professional business card with more than just logo and demographic info. Something memorable.

We are a trendy/modern chiropractic group with an emphasis on neurology, hence the minimalist-type brain logo. We want to convey that modern and technical aspect with professionalism and the elite nature of our practice environment.

```html
<!DOCTYPE html>
<html lang="en">
<head>
<meta charset="utf-8">
<title>Meridian Spine – Business Card</title>
<link rel="stylesheet" href="https://fonts.googleapis.com/css2?family=Arimo:wght@400;700&family=Libre+Baskerville:wght@700&display=swap">
<style>
  :root {
    --backdrop: #0b0b0c;
    --card: #262729;
    --card-back: #2a2b2d;
    --edge-blue: #3f78c4;
    --accent-blue: #4a86d2;
    --text-light: #e9eaec;
    --text-muted: #b9bcc1;
    --emboss: #55575b;
  }
  * { box-sizing: border-box; margin: 0; padding: 0; }
  html, body {
    width: 1200px; height: 822px; overflow: hidden;
    background: var(--backdrop);
    font-family: "Arimo", Arial, sans-serif;
  }
  .stage {
    width: 1200px; height: 822px;
    display: flex; align-items: center; justify-content: center; gap: 60px;
  }
  .card {
    width: 500px; height: 286px;
    border-radius: 3px;
    position: relative;
    box-shadow: 0 3px 0 var(--edge-blue), 0 18px 40px rgba(0,0,0,.6);
  }
  .card--front { background: var(--card); padding: 44px 0 0 56px; }
  .card--back {
    background: var(--card-back);
    display: flex; align-items: center; justify-content: center; gap: 16px;
  }
  .brand { display: flex; align-items: center; gap: 14px; }
  .brand__square { width: 38px; height: 38px; background: var(--accent-blue); }
  .brand__name {
    font-weight: 700; font-size: 34px; letter-spacing: 2px;
    color: var(--text-light); text-transform: uppercase;
  }
  .card--back .brand__square { background: var(--emboss); }
  .card--back .brand__name { color: var(--emboss); }
  .person { margin: 26px 0 0 52px; }
  .person__name {
    font-family: "Libre Baskerville", Georgia, serif;
    font-weight: 700; font-size: 17px; color: var(--accent-blue);
    text-transform: uppercase; letter-spacing: .5px;
  }
  .person__title { font-size: 12px; color: var(--text-muted); text-transform: uppercase; margin-top: 2px; }
  .contact { margin: 16px 0 0 52px; list-style: none; font-size: 12.5px; color: var(--text-light); line-height: 1.45; text-transform: uppercase; }
  .address { position: absolute; left: 56px; bottom: 28px; font-size: 12.5px; color: var(--text-light); text-transform: uppercase; }
</style>
</head>
<body>
  <main class="stage">
    <section class="card card--front" aria-label="Business card front">
      <div class="brand">
        <span class="brand__square"></span>
        <span class="brand__name">Meridian Spine</span>
      </div>
      <div class="person">
        <p class="person__name">Daniel Harper</p>
        <p class="person__title">Managing Director</p>
      </div>
      <ul class="contact">
        <li>044-555 010 234</li>
        <li>hello@meridianspine.com</li>
        <li>www.meridianspine.com</li>
      </ul>
      <p class="address">88 Harbor Lane, Springfield, 60120</p>
    </section>
    <section class="card card--back" aria-label="Business card back">
      <div class="brand">
        <span class="brand__square"></span>
        <span class="brand__name">Meridian Spine</span>
      </div>
    </section>
  </main>
</body>
</html>
```